Corvel Capital LLC

Need Professional Business cards for New Investment Fund

Target Market(s)

High Quality investors

Industry/Entity Type

Financial

Contact Information for Business Card

Phone Number +1 555 284 6190
Name Lukas Varenko
Title Fund Manager
email lv@FundCorvel.com
Website www.FundCorvel.com

Colors

Designer to choose colors to be used in the design.

Requirements
Must have
• Must have our Logo and all of the above. Must be made so lettering and loge can be raised

```html
<!DOCTYPE html>
<html lang="en">
<head>
<meta charset="utf-8">
<title>Quenvale – Business Card</title>
<link rel="stylesheet" href="https://fonts.googleapis.com/css2?family=Jost:wght@500;600&family=Raleway:wght@400&display=swap">
<style>
  :root {
    --stage: #1f1f1f;
    --green: #5aba47;
    --slate: #434f42;
    --white: #ffffff;
    --ink: #3c4a3c;
  }
  * { box-sizing: border-box; margin: 0; padding: 0; }
  html, body { width: 1200px; height: 900px; overflow: hidden; }
  body {
    background: var(--stage);
    position: relative;
    font-family: "Raleway", sans-serif;
  }
  .card {
    position: absolute;
    left: 250px;
    width: 700px;
    height: 400px;
    overflow: hidden;
  }
  .card--front { top: 40px; background: var(--green); }
  .card--back  { top: 470px; background: var(--slate); }

  .brand {
    position: absolute;
    display: flex;
    align-items: center;
    gap: 12px;
    font-family: "Jost", sans-serif;
    font-weight: 600;
    letter-spacing: 0.06em;
    text-transform: uppercase;
    color: var(--white);
    white-space: nowrap;
  }
  .card--front .brand {
    left: 50%; top: 50%;
    transform: translate(-50%, -50%);
    font-size: 52px;
  }
  .card--front .brand-square {
    width: 30px; height: 30px; background: var(--ink);
  }
  .card--back .brand {
    right: 50px; top: 96px;
    font-size: 32px;
  }
  .card--back .brand-square {
    width: 20px; height: 20px; background: var(--green);
  }

  .divider {
    position: absolute;
    left: 80px; top: 222px;
    width: 580px; height: 2px;
    background: var(--green);
  }
  .accent-bar {
    position: absolute;
    left: 0; top: 246px;
    width: 8px; height: 42px;
    background: var(--green);
  }
  .holder {
    position: absolute;
    left: 50px; top: 240px;
    color: var(--white);
  }
  .holder-name {
    font-family: "Jost", sans-serif;
    font-weight: 600;
    font-size: 30px;
    letter-spacing: 0.03em;
    text-transform: uppercase;
    line-height: 1.15;
  }
  .holder-title {
    font-size: 20px;
    margin-top: 2px;
  }
  .contacts {
    position: absolute;
    right: 40px; top: 284px;
    list-style: none;
    color: var(--white);
    font-size: 22px;
    letter-spacing: 0.02em;
  }
  .contacts li {
    display: flex;
    align-items: center;
    justify-content: flex-end;
    gap: 14px;
    height: 34px;
  }
  .contacts svg {
    width: 20px; height: 20px;
    fill: none; stroke: var(--green); stroke-width: 2;
  }
</style>
</head>
<body>
  <section class="card card--front" aria-label="Card front">
    <div class="brand"><span class="brand-square"></span>Quenvale</div>
  </section>

  <section class="card card--back" aria-label="Card back">
    <div class="brand"><span class="brand-square"></span>Quenvale</div>
    <div class="divider"></div>
    <div class="accent-bar"></div>
    <div class="holder">
      <p class="holder-name">Lukas Varenko</p>
      <p class="holder-title">Title Fund Manager</p>
    </div>
    <ul class="contacts">
      <li>+1 555 284 6190
        <svg viewBox="0 0 24 24" aria-hidden="true"><path fill="#5aba47" stroke="none" d="M6.6 3.5l3 3.2-1.7 2.3c1 2.2 2.9 4.2 5.1 5.2l2.3-1.7 3.2 3-1.6 2.9C10.7 18.3 5.7 13.3 3.6 5.1z"/></svg>
      </li>
      <li>lv@FundCorvel.com
        <svg viewBox="0 0 24 24" aria-hidden="true"><rect x="3" y="6" width="18" height="12"/><path d="M3 6l9 7 9-7"/></svg>
      </li>
      <li>www.FundCorvel.com
        <svg viewBox="0 0 24 24" aria-hidden="true"><circle cx="12" cy="12" r="9"/><ellipse cx="12" cy="12" rx="4" ry="9"/><path d="M3 12h18M5 7h14M5 17h14"/></svg>
      </li>
    </ul>
  </section>
</body>
</html>
```